Catalogue Design Project

We need a catalog design for a new private university called Redwell Institute Bayshore (see website www.rwi-bs.org). The catalog should be about 30 pages maximum and will include items such as General Information, Academic schedule, department descriptions, program descriptions, course descriptions, school policies, student services, admissions, San diego Lifestyle, etc.
I will provide the text but I need a professional design with regard to page layouts. I have provided some examples.
Ok, i posted the catalog content, just missing course descriptions.
Target Market(s)
Young Professionals, Foreign Students
Industry/Entity Type
University
Look and feel
Each slider illustrates characteristics of the customer's brand and the style your logo design should communicate.

```html
<!DOCTYPE html>
<html lang="en">
<head>
<meta charset="utf-8">
<title>San Diego Life Style – Redwell Institute Bayshore</title>
<link href="https://fonts.googleapis.com/css2?family=Carlito:wght@400;700&display=swap" rel="stylesheet">
<style>
  :root {
    --brand-navy: #2b4f7e;
    --rule-blue: #3d6598;
    --body-grey: #6b6b6b;
    --footer-grey: #8a8a8a;
    --rule-grey: #b9bcc2;
    --paper: #ffffff;
    --sky-top: #9fd4ef;
    --sky-low: #cfe9f6;
    --tower: #6f9fa8;
    --harbour: #2f9bb8;
    --tank-deep: #0f4f52;
    --tank-mid: #2f8d86;
    --tank-light: #7fc7b8;
    --bear-light: #e8e6de;
    --bear-shadow: #5b5a55;
  }
  * { margin: 0; padding: 0; box-sizing: border-box; }
  html, body { width: 927px; height: 1200px; overflow: hidden; background: var(--paper); }
  .page {
    position: relative;
    width: 927px;
    height: 1200px;
    background: var(--paper);
    font-family: "Carlito", "Calibri", Arial, sans-serif;
    color: var(--body-grey);
  }
  .section-tab {
    position: absolute;
    top: 18px;
    right: 0;
    width: 344px;
    height: 38px;
    background: var(--brand-navy);
    clip-path: polygon(14px 0, 100% 0, 100% 100%, 0 100%);
    color: var(--paper);
    font-size: 23px;
    letter-spacing: 0.3px;
    line-height: 38px;
    padding-left: 52px;
    text-transform: uppercase;
  }
  .header-rule {
    position: absolute;
    top: 55px;
    left: 0;
    width: 927px;
    height: 2px;
    background: var(--rule-blue);
  }
  .photo-skyline {
    position: absolute;
    top: 58px;
    left: 0;
    width: 927px;
    height: 510px;
    background: linear-gradient(180deg, var(--sky-top) 0%, var(--sky-low) 45%, var(--tower) 72%, var(--harbour) 86%, #1f86a5 100%);
  }
  .photo-aquarium {
    position: absolute;
    top: 477px;
    left: 470px;
    width: 457px;
    height: 349px;
    background: radial-gradient(ellipse at 55% 25%, var(--tank-light) 0%, var(--tank-mid) 45%, var(--tank-deep) 100%);
    border-left: 3px solid var(--paper);
    border-top: 3px solid var(--paper);
  }
  .photo-bear {
    position: absolute;
    top: 385px;
    left: 691px;
    width: 196px;
    height: 196px;
    border-radius: 50%;
    border: 4px solid var(--paper);
    background: radial-gradient(circle at 55% 50%, var(--bear-light) 0%, #b9b7ae 45%, var(--bear-shadow) 100%);
  }
  .intro-copy {
    position: absolute;
    top: 616px;
    left: 48px;
    width: 392px;
    font-size: 19px;
    line-height: 24.6px;
    text-align: justify;
  }
  .closing-copy {
    position: absolute;
    top: 884px;
    left: 476px;
    width: 412px;
    font-size: 19px;
    line-height: 24.6px;
  }
  .footer-rule {
    position: absolute;
    top: 1167px;
    left: 0;
    width: 927px;
    height: 2px;
    background: var(--rule-grey);
  }
  .page-footer {
    position: absolute;
    top: 1175px;
    right: 34px;
    font-size: 13px;
    color: var(--footer-grey);
    letter-spacing: 0.2px;
  }
</style>
</head>
<body>
  <main class="page">
    <div class="section-tab">San Diego Life Style</div>
    <div class="header-rule"></div>

    <div class="photo-skyline" role="img" aria-label="Photo of the San Diego downtown skyline with high-rise towers and harbour boats under a clear blue sky"></div>
    <div class="photo-aquarium" role="img" aria-label="Photo of visitors viewing a large kelp forest aquarium tank with schools of fish"></div>
    <div class="photo-bear" role="img" aria-label="Circular photo of a polar bear at the wildlife garden"></div>

    <p class="intro-copy">Welcome to San Diego, California’s second largest city and home to 70 miles of blue skies and beautiful coastline. Bordered by the Anza-Borrego Desert to the east, Mexico to the south, and the Pacific Ocean to the west, San Diego is spread out over 4000 square miles and is a city where you can have it all. The Mediterranean climate affords its residents the best weather in the world year round allowing for trips to the beach to relax or enjoy watersports, shop, go hiking or camping. One can also explore San Diego’s downtown, the iconic Gaslamp District, the charming island town of Coronado or the luxurious village of La Jolla. San Diego is also home to the Bayview Wildlife Garden, arguably the world’s best not to mention home to the Mesa Safari Reserve and Harbor Marine Park. Visitors can also visit Los Angeles, go skiing, wine tasting, or skiing within a short drive.</p>

    <p class="closing-copy">San Diego truly is America’s finest city – don’t miss out on an opportunity to study here at RWIB and take it all in.</p>

    <div class="footer-rule"></div>
    <footer class="page-footer">26::: REDWELL INSTITUTE</footer>
  </main>
</body>
</html>
```